WP website design (Tarnwick)

We need a wordpress design for an established auction and real estate company based in Arkansas. The winning design will incorporate a professional color scheme with company logo in a clean layout. The design needs to consider that this will be developed on a responsive theme.

Industry/Entity Type

Real Estate

Font styles to use
Sans Serif

Colors

Designer to choose colors to be used in the design.

Requirements
Must have
• Site will have slideshow, please use stock real estate or other image. A rough idea of homepage content is attached - not necessarily for design purposes.

Navigation Structure is:
1) Home
2) Auctions
3) Services
4) For Sale
5) About Us
6) Ned Videos
7) News & Events
8) Contact Us

Widgets will include:
Social media icons (Friendly, Youtube, RSS)
Testimonials Widget - this should be prominent
Featured Video
Email Signup form (Sign up to receive exclusive email updates for Tarnwick auctions. )
Nice to have
• A drop down menu example
Should not have
• no gavel in the design

```html
<!DOCTYPE html>
<html lang="en">
<head>
<meta charset="utf-8">
<title>Tarnwick Auction &amp; Marketing</title>
<link href="https://fonts.googleapis.com/css2?family=Ubuntu:wght@300;400;500&family=PT+Serif:wght@400;700&family=Open+Sans:wght@400;600&display=swap" rel="stylesheet">
<style>
:root{
  --green:#0e7a3a;
  --green-dark:#0a5e2c;
  --green-soft:#d4e8dc;
  --ink:#222;
  --muted:#555;
  --line:#ddd;
  --black:#1b1b1b;
  --red:#c8102e;
}
*{box-sizing:border-box;margin:0;padding:0}
html,body{width:856px;height:1200px;overflow:hidden}
body{position:relative;font-family:"Open Sans",Arial,sans-serif;color:var(--ink);
  background:linear-gradient(180deg,#0f7a3b 0,#3f9a62 120px,#a9d2b6 260px,#fff 380px)}
.abs{position:absolute}
.page{position:absolute;left:80px;top:0;width:688px;height:1087px;background:#fff}
.header{left:80px;top:0;width:688px;height:74px;background:#fff}
.brand{left:92px;top:18px;font-family:"Ubuntu",sans-serif;font-weight:500;font-size:34px;letter-spacing:1px;color:var(--green-dark);display:flex;align-items:center;gap:8px}
.brand-mark{width:14px;height:14px;background:var(--green);border-radius:50%}
.brand-sub{left:102px;top:55px;font-family:"Ubuntu",sans-serif;font-size:13px;letter-spacing:1.5px;color:var(--green-dark)}
.signin{left:449px;top:27px;width:121px;height:20px;background:linear-gradient(#6f8fd0,#4a68b5);border-radius:3px;color:#fff;font-size:8px;font-weight:600;display:flex;align-items:center;padding-left:8px;gap:6px;white-space:nowrap}
.signin i{width:9px;height:9px;background:#fff;display:block}
.phone{right:101px;top:16px;font-family:"Ubuntu",sans-serif;font-size:17px;color:var(--green);display:flex;align-items:center;gap:6px}
.contact-name{right:101px;top:45px;font-size:10px;color:var(--green)}
.contact-mail{right:101px;top:59px;font-size:9px;color:#111}
.nav{left:80px;top:74px;width:688px;height:31px;background:var(--black);display:flex}
.nav a{font-family:"PT Serif",serif;font-size:11.5px;color:#fff;text-decoration:none;display:flex;align-items:center;justify-content:center;white-space:nowrap;border-right:1px solid #3a3a3a;flex:none}
.nav a.active{background:var(--green)}
.slide{left:95px;top:123px;width:452px;height:218px;background:linear-gradient(180deg,#cfe0ee 0,#e9eef0 40%,#9aa59a 85%,#6f7d6a);}
.caption{left:95px;top:314px;width:452px;height:27px;background:rgba(0,0,0,.75);color:#fff;font-family:"PT Serif",serif;font-size:11px;display:flex;align-items:center;padding-left:13px}
.dots{left:501px;top:322px;display:flex;gap:2px}
.dots span{width:10px;height:10px;border:1.5px solid #fff;border-radius:50%}
.dots span:first-child{background:var(--red)}
.agent{left:579px;top:123px;width:176px;height:218px;background:linear-gradient(180deg,#dfe8f1,#b7c6d6 60%,#8193a7)}
.agent-bar{left:579px;top:314px;width:176px;height:27px;background:rgba(0,0,0,.75);color:#fff;font-size:9px;display:flex;align-items:center;justify-content:space-between;padding:0 10px}
.agent-bar b{font-weight:400;font-size:11px}
.h2{font-family:"Ubuntu",sans-serif;font-weight:300;font-size:18px;color:#222}
.h2 em{font-style:normal;color:var(--green)}
.card{left:86px;width:474px;border:1px solid var(--line);background:#fff}
.card-head{position:absolute;left:4px;top:3px;width:464px;height:25px;background:var(--green);color:#fff;font-family:"Ubuntu",sans-serif;font-size:13px;display:flex;align-items:center;padding-left:14px}
.card-head.soft{background:var(--green-soft);color:#222;border:1px solid #bfd8c8}
.thumb{position:absolute;left:6px;top:36px;width:160px;height:105px}
.info{position:absolute;left:174px;top:38px;width:201px;font-size:8.5px;color:var(--muted);line-height:13px;border-right:1px solid var(--line);height:104px;white-space:nowrap}
.info h3{font-family:"Ubuntu",sans-serif;font-weight:400;font-size:11px;color:#111;margin-bottom:6px}
.info .more{color:var(--red)}
.links{position:absolute;left:385px;top:80px;font-size:9px;color:#444;line-height:23px;white-space:nowrap}
.links div{display:flex;align-items:center;gap:7px}
.testi{left:576px;width:185px}
.face{position:absolute;left:0;top:0;width:48px;height:52px;border:2px solid #fff;box-shadow:0 0 2px #999;background:linear-gradient(#e0c6b0,#b08d76)}
.bubble{position:absolute;left:58px;top:0;width:126px;height:62px;border:1px solid var(--line);border-radius:3px;font-size:7.3px;color:#444;line-height:12.5px;padding:6px 4px;box-shadow:0 1px 2px #ccc;letter-spacing:-.1px}
.bubble span{display:block;text-align:right;color:var(--red);padding-right:4px}
.arrows{left:734px;top:368px;display:flex;gap:7px}
.arrows i{width:8px;height:8px;background:#d33;display:block}
.search{left:576px;top:557px;width:184px;height:20px;border:1px solid #bbb;border-radius:3px;font-size:8px;color:#777;display:flex;align-items:center;padding-left:30px}
.search b{position:absolute;right:-1px;top:-1px;height:20px;width:29px;background:var(--green);color:#fff;font-weight:400;display:flex;align-items:center;justify-content:center;border-radius:0 3px 3px 0}
.signup{left:576px;top:593px;width:184px;height:170px;background:var(--green);border-radius:3px;border:2px solid #cfe3d6}
.signup h4{position:absolute;left:40px;top:8px;font-family:"Ubuntu",sans-serif;font-weight:500;font-size:15px;color:#fff;font-variant:small-caps}
.envelope{position:absolute;left:12px;top:6px;width:22px;height:18px;background:#fff;transform:rotate(-12deg)}
.field{position:absolute;left:7px;width:168px;height:21px;background:#fff;border-radius:2px;font-size:7.5px;font-style:italic;color:#999;padding:6px 11px}
.submit{position:absolute;left:87px;top:138px;width:86px;height:21px;background:linear-gradient(#444,#111);color:#fff;font-size:10px;border-radius:3px;display:flex;align-items:center;justify-content:center}
.box{left:576px;width:184px;border:1px solid var(--line);border-radius:3px;background:#fff}
.partners h4{font-family:"Ubuntu",sans-serif;font-size:11px;font-weight:500;color:var(--green);font-variant:small-caps;margin:12px 0 0 20px}
.badges{display:flex;gap:4px;margin:10px 0 0 38px}
.badges i{width:24px;height:22px;background:#d0d4da;display:block}
.connect h4{font-family:"PT Serif",serif;font-size:13px;color:var(--green-dark);margin:10px 0 0 20px}
.social{display:grid;grid-template-columns:1fr 1fr;row-gap:10px;margin:12px 20px 0 8px;font-size:9px;color:#222}
.social div{display:flex;justify-content:flex-end;align-items:center;gap:8px}
.social i{width:15px;height:15px;border-radius:2px;display:block}
.video{left:92px;top:925px;width:198px;height:125px;background:linear-gradient(180deg,#8a8f90 0,#6b6050 50%,#2a2a2a)}
.vtext{left:304px;top:925px;width:254px;font-size:8.5px;line-height:12px;color:#333;text-align:justify}
.morebtn{left:306px;top:1023px;width:58px;height:21px;background:var(--green);color:#fff;font-size:8.5px;border-radius:3px;display:flex;align-items:center;justify-content:center}
.footer{left:80px;top:1087px;width:688px;height:81px;background:var(--black);color:#ddd;font-size:8.5px;text-align:center;padding-top:27px;line-height:17px}
</style>
</head>
<body>
<div class="page"></div>

<header class="abs header"></header>
<div class="abs brand"><span>TARNWICK</span><span class="brand-mark"></span></div>
<div class="abs brand-sub">AUCTION &amp; MARKETING, LLC</div>
<div class="abs signin"><i></i>Sign in with Friendly</div>
<div class="abs phone">
  <svg width="22" height="14" viewBox="0 0 22 14"><path d="M2 5c3-4 15-4 18 0l-3 2-2-2H7L5 7z" fill="#333"/><rect x="5" y="7" width="12" height="6" rx="1" fill="#333"/></svg>
  1-800-555-0147</div>
<div class="abs contact-name">Ned Garrow</div>
<div class="abs contact-mail">NedGarrow@tarnwick.com</div>

<nav class="abs nav">
  <a class="active" style="width:70px">Home</a><a style="width:82px">Auctions</a><a style="width:76px">Services</a><a style="width:76px">For Sale</a><a style="width:86px">About Us</a><a style="width:92px">Ned Videos</a><a style="width:113px">News &amp; Events</a><a style="width:93px;border:none">Contact Us</a>
</nav>

<div class="abs slide" role="img" aria-label="White two-storey house with green shutters and an auction sign"></div>
<div class="abs caption">Specialising in Real Estate, form &amp; Ranch, Form Implement...</div>
<div class="abs dots"><span></span><span></span><span></span></div>
<div class="abs agent" role="img" aria-label="Portrait of the auctioneer in shirt and tie"></div>
<div class="abs agent-bar"><b>Ned Garrow</b><span>License #20458</span></div>

<div class="abs h2" style="left:86px;top:361px">Current <em>Auctions</em></div>

<section class="abs card" style="top:395px;height:151px">
  <div class="card-head">Real Estate Auction</div>
  <div class="thumb" role="img" aria-label="Large cream house" style="background:linear-gradient(#b9d3ee,#e8e1cf 55%,#6e8a5e)"></div>
  <div class="info"><h3>Live On-Site Auction</h3>Begins: &nbsp;Friday, March 14, 2014 at 7:00 PM EDT<br>Location:<br>Ridgeview College<br>Mercer Commons<br>Fairbury, AR 72001<br><span class="more">More &gt;&gt;</span></div>
  <div class="links"><div><svg width="11" height="11"><circle cx="4.5" cy="4.5" r="3.3" stroke="#222" stroke-width="1.6" fill="none"/><path d="M7 7l3.5 3.5" stroke="#222" stroke-width="1.8"/></svg>Details</div><div><svg width="15" height="11"><path d="M1 3l12-2 1 7-12 2z" stroke="#222" stroke-width="1.4" fill="none"/></svg>Photo Galleries</div></div>
</section>

<section class="abs card" style="top:555px;height:151px">
  <div class="card-head soft">Estate Auction</div>
  <div class="thumb" role="img" aria-label="White estate mansion under blue sky" style="background:linear-gradient(#3f74c0,#c8d8ea 50%,#4f7a3c)"></div>
  <div class="info"><h3>Live On-Site Auction</h3>Begins: &nbsp;Friday, March 14, 2014 at 7:00 PM EDT<br>Location:<br>Ridgeview College<br>Mercer Commons<br>Fairbury, AR 72001<br><span class="more">More &gt;&gt;</span></div>
  <div class="links"><div><svg width="11" height="11"><circle cx="4.5" cy="4.5" r="3.3" stroke="#222" stroke-width="1.6" fill="none"/><path d="M7 7l3.5 3.5" stroke="#222" stroke-width="1.8"/></svg>Details</div><div><svg width="15" height="11"><path d="M1 3l12-2 1 7-12 2z" stroke="#222" stroke-width="1.4" fill="none"/></svg>Photo Galleries</div></div>
</section>

<section class="abs card" style="top:720px;height:151px">
  <div class="card-head">Auction</div>
  <div class="thumb" role="img" aria-label="Lot of parked cars with a white sports car in front" style="background:linear-gradient(#9cb0c6,#d9d9d9 45%,#777 100%)"></div>
  <div class="info"><h3>Live On-Site Auction</h3>Begins: &nbsp;Friday, March 14, 2014 at 7:00 PM EDT<br>Location:<br>Ridgeview College<br>Mercer Commons<br>Fairbury, AR 72001<br><span class="more">More &gt;&gt;</span></div>
  <div class="links"><div><svg width="11" height="11"><circle cx="4.5" cy="4.5" r="3.3" stroke="#222" stroke-width="1.6" fill="none"/><path d="M7 7l3.5 3.5" stroke="#222" stroke-width="1.8"/></svg>Details</div><div><svg width="15" height="11"><path d="M1 3l12-2 1 7-12 2z" stroke="#222" stroke-width="1.4" fill="none"/></svg>Photo Galleries</div></div>
</section>

<div class="abs h2" style="left:573px;top:364px;font-size:16px">Testimonials</div>
<div class="abs arrows"><i></i><i></i></div>
<div class="abs testi" style="top:396px;height:62px">
  <div class="face" role="img" aria-label="Photo of John"></div>
  <div class="bubble">Uenim ad minim veniam, quis laboris &nbsp;nisi utaliquip ex irurdolor into Uenim ad minim veniam.<span>John</span></div>
</div>
<div class="abs testi" style="top:479px;height:62px">
  <div class="face" role="img" aria-label="Photo of Mary" style="background:linear-gradient(#8a5a3a,#d9b49a)"></div>
  <div class="bubble" style="left:62px">Uenim ad minim veniam, quis laboris &nbsp;nisi utaliquip ex irurdolor into Uenim ad minim veniam.<span>Mary</span></div>
</div>

<div class="abs search">
  <svg class="abs" style="left:11px;top:4px" width="11" height="11"><circle cx="4.5" cy="4.5" r="3.3" stroke="#888" stroke-width="1.4" fill="none"/><path d="M7 7l3.5 3.5" stroke="#888" stroke-width="1.6"/></svg>
  Search<b>GO</b></div>

<form class="abs signup">
  <div class="envelope"></div>
  <h4>Email Signup</h4>
  <div class="field" style="top:45px">Name</div>
  <div class="field" style="top:75px">Phone</div>
  <div class="field" style="top:104px">Email</div>
  <div class="submit">Submit Now</div>
</form>

<div class="abs box partners" style="top:780px;height:83px">
  <h4>Partners</h4>
  <div class="badges"><i></i><i style="width:18px"></i><i></i></div>
</div>

<div class="abs box connect" style="top:880px;height:126px">
  <h4>Connect With Us</h4>
  <div class="social">
    <div>Friendly<i style="background:#3b5998"></i></div>
    <div>WorkLink<i style="background:#1a7ab5"></i></div>
    <div>Chirp<i style="background:#3cb0e6"></i></div>
    <div>Orbit +1<i style="background:#4a9a3a"></i></div>
    <div>RSS<i style="background:#f08020"></i></div>
    <div>Pinboard<i style="background:#d22b36"></i></div>
  </div>
</div>

<div class="abs h2" style="left:90px;top:890px;font-size:15px">Featured <em style="color:var(--red)">Video</em></div>
<div class="abs" style="left:90px;top:915px;width:430px;height:1px;background:var(--line)"></div>
<div class="abs video" role="img" aria-label="Video still of a house with a yellow auction sign"></div>
<svg class="abs" style="left:176px;top:970px" width="26" height="18"><rect width="26" height="18" rx="3" fill="#111"/><path d="M10 4l8 5-8 5z" fill="#fff"/></svg>
<div class="abs vtext">Sed ut perspiciatis unde omnis iste natus error sit voluptatem accusantium doloremque laudantium, totam rem aperiam, eaque ipsa quae ab illo inventore veritatis et quasi architecto beatae vitae dicta sunt explicabo.<br>Nemo enim ipsam voluptatem quia voluptas sit aspernatur aut odit aut fugit, sed quia consequuntur magni dolores eos qui ratione voluptatem sequi nesciunt.</div>
<div class="abs morebtn">MORE</div>

<footer class="abs footer">Privacy Policy &nbsp;| &nbsp;FAQ &nbsp;| &nbsp;Terms<br>© &nbsp;2014 Tarnwick. All rights reserved.</footer>
</body>
</html>
```